Business card for medical clinic

I need an upmarket, modern medical/health business card for my clinic

Contact Information for Business Card

name, address, email, qr code

```html
<!DOCTYPE html>
<html lang="en">
<head>
<meta charset="utf-8">
<title>Corvana Health Partners – Business Card</title>
<link rel="stylesheet" href="https://fonts.googleapis.com/css2?family=Cinzel:wght@500&family=PT+Serif&display=swap">
<style>
  :root {
    --backdrop: #6d6d70;
    --card-dark: #161616;
    --card-light: #ffffff;
    --brand-blue: #1f74b3;
    --accent-blue: #2a9ad8;
    --ink: #2b2b2b;
  }
  * { margin: 0; padding: 0; box-sizing: border-box; }
  html, body {
    width: 900px;
    height: 1200px;
    overflow: hidden;
    background: var(--backdrop);
  }
  .card {
    position: absolute;
    left: 133px;
    width: 633px;
    height: 364px;
  }
  .card--front { top: 210px; background: var(--card-dark); }
  .card--back  { top: 624px; background: var(--card-light); }

  .brand {
    position: absolute;
    text-align: center;
    font-family: "Cinzel", serif;
    font-weight: 500;
    line-height: 1.1;
    letter-spacing: 0.02em;
    white-space: nowrap;
  }
  .brand__sub { display: block; letter-spacing: 0.32em; }

  .card--front .brand {
    left: 0;
    right: 0;
    top: 148px;
    color: var(--accent-blue);
    font-size: 33px;
  }
  .card--front .brand__sub { font-size: 16px; margin-top: 4px; }

  .card--back .brand {
    left: 36px;
    width: 260px;
    top: 160px;
    color: var(--brand-blue);
    font-size: 24px;
  }
  .card--back .brand__sub { font-size: 12px; margin-top: 3px; }

  .divider {
    position: absolute;
    left: 316px;
    top: 94px;
    width: 2px;
    height: 178px;
    background: linear-gradient(to bottom, #1d3f66, var(--accent-blue));
  }
  .details {
    position: absolute;
    left: 330px;
    top: 90px;
    font-family: "PT Serif", serif;
    color: var(--ink);
    font-size: 14.5px;
    line-height: 22px;
  }
  .details__name {
    font-family: "Cinzel", serif;
    font-weight: 500;
    font-size: 21px;
    color: var(--brand-blue);
    line-height: 26px;
  }
  .details__role { margin-bottom: 10px; }
  .details__address { margin-bottom: 12px; }
  .contact-line {
    display: flex;
    align-items: center;
    gap: 7px;
    height: 25px;
  }
  .contact-line svg { width: 12px; height: 12px; fill: var(--brand-blue); flex: none; }
  .contact-line--phone { letter-spacing: 0.18em; }
</style>
</head>
<body>

<section class="card card--front">
  <p class="brand">CORVANA HEALTH<span class="brand__sub">PARTNERS</span></p>
</section>

<section class="card card--back">
  <p class="brand">CORVANA HEALTH<span class="brand__sub">PARTNERS</span></p>

  <div class="divider"></div>

  <div class="details">
    <p class="details__name">DANIEL WHITFORD</p>
    <p class="details__role">Principal Consultant</p>
    <p class="details__address">PO Box 481520<br>Birch Hollow, Alaska 99602</p>

    <p class="contact-line contact-line--phone">
      <svg viewBox="0 0 24 24" aria-hidden="true"><path d="M6.6 10.8a15.1 15.1 0 0 0 6.6 6.6l2.2-2.2a1 1 0 0 1 1-.25 11.4 11.4 0 0 0 3.6.57 1 1 0 0 1 1 1V20a1 1 0 0 1-1 1A17 17 0 0 1 3 4a1 1 0 0 1 1-1h3.5a1 1 0 0 1 1 1c0 1.25.2 2.450.57 3.57a1 1 0 0 1-.25 1z"/></svg>
      +1-907-555-0142
    </p>
    <p class="contact-line">
      <svg viewBox="0 0 24 24" aria-hidden="true"><path d="M2 5h20v14H2z M2 5l10 8 10-8" fill="none" stroke="#1f74b3" stroke-width="2.4"/></svg>
      info@corvanahealthpartners.com
    </p>
    <p class="contact-line">
      <svg viewBox="0 0 24 24" aria-hidden="true"><g fill="none" stroke="#1f74b3" stroke-width="2"><circle cx="12" cy="12" r="10"/><ellipse cx="12" cy="12" rx="4.5" ry="10"/><path d="M2 12h20M4 6.5h16M4 17.5h16"/></g></svg>
      www.corvanahealthpartners.com
    </p>
  </div>
</section>

</body>
</html>
```